Free range pig farm business

We'd like a simple but elegant website for our new free range pig farm business.
Check out www.kelvorrahogsteads.com.au and http://www.tirrowfield.com.au/
pages:
Home
About
Shop
Contact
Target Market(s)
People who would want to find out where they could buy our pork
Industry/Entity Type
Agribusiness
Number of Pages Required
4 page
Font styles to use
Other font styles liked:
- As per our logo
Requirements
Must have
- Ability for us to update weekly with new news and photos

```html
<!DOCTYPE html>
<html lang="en">
<head>
<meta charset="utf-8">
<title>Southern Meadow Pork</title>
<link rel="stylesheet" href="https://fonts.googleapis.com/css2?family=Arvo:wght@400;700&family=Open+Sans:wght@400;600;700&display=swap">
<style>
:root{
  --cream:#e7e0cd;
  --cream-dark:#d8cfb6;
  --brown:#4a3a33;
  --brown-deep:#3e302a;
  --green:#a6c12f;
  --green-bright:#b9d433;
  --text:#5a514a;
  --heading:#3f322c;
  --price:#c8403c;
  --white:#ffffff;
}
*{margin:0;padding:0;box-sizing:border-box}
html,body{width:1200px;height:3579px;overflow:hidden}
body{background:var(--cream);font-family:"Open Sans",sans-serif;color:var(--text);position:relative}
.btn{position:absolute;background:var(--green);color:var(--white);font:700 13px "Open Sans",sans-serif;letter-spacing:1px;text-transform:uppercase;border-radius:22px;display:flex;align-items:center;justify-content:center}

/* header */
.site-header{position:absolute;left:0;top:0;width:1200px;height:84px;background:var(--cream);z-index:3}
.nav-link{position:absolute;top:32px;font:600 15px "Open Sans",sans-serif;color:var(--heading);text-transform:uppercase;letter-spacing:.5px}
.login{top:24px;left:1002px;width:96px;height:36px;font-size:13px}
.brand-tab{position:absolute;left:480px;top:-70px;width:240px;height:242px;border-radius:50%;background:var(--cream);z-index:4;display:flex;flex-direction:column;align-items:center;justify-content:flex-end;padding-bottom:44px}
.brand-dot{width:46px;height:46px;border-radius:50%;background:var(--green);margin-bottom:10px}
.brand-name{font:700 17px "Arvo",serif;color:var(--heading);text-align:center;line-height:1.25;width:170px}

/* hero */
.hero{position:absolute;left:0;top:0;width:1200px;height:701px;background:linear-gradient(180deg,#8ea2a4 0%,#6f8a62 14%,#5f7f3f 30%,#6e8f3a 55%,#587534 100%)}
.hero-title{position:absolute;left:0;width:1200px;top:328px;text-align:center;font:400 45px "Arvo",serif;color:var(--green-bright);letter-spacing:2px;text-transform:uppercase}
.hero-sub{position:absolute;left:0;width:1200px;top:390px;text-align:center;font:400 25px "Arvo",serif;color:var(--white)}
.hero-btn{left:503px;top:443px;width:194px;height:44px}
.dots{position:absolute;display:flex;gap:8px}
.dots span{width:8px;height:8px;border-radius:50%;background:rgba(255,255,255,.6)}
.dots span.on{background:var(--green)}

/* welcome */
.welcome{position:absolute;left:0;top:701px;width:1200px;height:583px;background:var(--cream)}
.mascot{position:absolute;left:180px;top:58px;width:250px;height:482px;border-radius:120px 120px 90px 90px;background:linear-gradient(180deg,#d6cfbc,#c3bba5)}
.welcome-h{position:absolute;left:587px;top:112px;font:700 38px "Arvo",serif;color:var(--heading);line-height:1.15}
.welcome-h small{display:block;font-size:27px;letter-spacing:1px}
.welcome-copy{position:absolute;left:587px;top:230px;width:520px;font-size:13px;line-height:26px}
.welcome-copy p+p{margin-top:24px}

/* farm */
.farm{position:absolute;left:0;top:1284px;width:1200px;height:558px;background:var(--brown)}
.farm-photo{position:absolute;left:0;top:0;width:599px;height:558px;background:radial-gradient(ellipse at 45% 60%,#d9a99a 0%,#9a6f5e 40%,#4b3a30 100%)}
.farm-h{position:absolute;right:83px;top:82px;font:400 48px "Arvo",serif;color:var(--white);letter-spacing:1px}
.farm-copy{position:absolute;right:83px;top:160px;width:450px;text-align:right;color:#e8e0d6;font-size:11.8px;line-height:26px}
.farm-copy p+p{margin-top:18px}
.farm-btn{left:933px;top:419px;width:188px;height:44px}

/* shop */
.shop{position:absolute;left:0;top:1842px;width:1200px;height:802px;background:var(--cream)}
.shop-h{position:absolute;left:0;width:1200px;top:88px;text-align:center;font:400 58px "Arvo",serif;color:var(--heading);letter-spacing:2px}
.shop-intro{position:absolute;left:180px;width:840px;top:172px;text-align:center;font-size:13px;line-height:27px}
.product{position:absolute;top:290px;width:360px}
.product-photo{position:absolute;left:44px;top:0;width:272px;height:272px;border-radius:50%;border:12px solid var(--cream-dark)}
.product-name{position:absolute;left:0;top:290px;width:360px;text-align:center;font:400 19px "Arvo",serif;color:var(--heading)}
.price{position:absolute;left:36px;top:335px;font:400 32px "Arvo",serif;color:var(--price)}
.shop-btn{left:180px;top:334px;width:146px;height:40px}

/* testimonial */
.testimonial{position:absolute;left:0;top:2644px;width:1200px;height:627px;background:var(--brown)}
.testimonial-photo{position:absolute;left:584px;top:0;width:616px;height:627px;clip-path:polygon(0 0,100% 0,100% 100%,37% 100%);background:radial-gradient(ellipse at 60% 55%,#dcb1a3 0%,#a97d6b 45%,#4c3d36 100%)}
.quote-mark{position:absolute;left:312px;top:96px}
.testimonial-copy{position:absolute;left:110px;width:450px;top:160px;text-align:center;color:#eee6dc;font-size:12px;line-height:29px}
.testimonial-copy p+p{margin-top:24px}
.avatar{position:absolute;left:170px;top:388px;width:118px;height:118px;border-radius:50%;border:5px solid #8a7b71;background:linear-gradient(180deg,#b79a85,#8e7361)}
.person{position:absolute;left:306px;top:428px;color:#fff;font:600 15px "Open Sans",sans-serif;letter-spacing:1px;text-transform:uppercase}
.person span{display:block;font:400 12px "Open Sans",sans-serif;letter-spacing:0;text-transform:none;margin-top:6px;color:#e2d8cd}

/* footer */
.site-footer{position:absolute;left:0;top:3271px;width:1200px;height:308px;background:var(--cream)}
.foot-h{font:600 14px "Open Sans",sans-serif;color:var(--heading);text-transform:uppercase;letter-spacing:1px;margin-bottom:16px}
.foot-col{position:absolute;top:52px;font-size:13px;line-height:29px}
.foot-col ul{list-style:none}
.email-field{width:330px;height:38px;border:1px solid #b8ad96;border-radius:20px;margin-top:20px;padding-left:20px;font-size:12px;line-height:36px;color:#8a8071}
.sub-btn{position:relative;margin-top:16px;width:124px;height:34px;font-size:12px}
.contact-line{display:flex;align-items:center;gap:10px}
.copyright{position:absolute;left:0;top:264px;width:1200px;text-align:center;font-size:13px;color:var(--text)}
</style>
</head>
<body>

<section class="hero" role="img" aria-label="Pigs grazing on a green hillside pasture"></section>

<header class="site-header">
  <a class="nav-link" style="left:110px">Home</a>
  <a class="nav-link" style="left:231px">About</a>
  <a class="nav-link" style="left:363px">Service</a>
  <a class="nav-link" style="left:764px">Shop</a>
  <a class="nav-link" style="left:883px">Contact</a>
  <a class="btn login">Login</a>
</header>
<div class="brand-tab">
  <span class="brand-dot"></span>
  <span class="brand-name">Southern Meadow Pork</span>
</div>

<h1 class="hero-title">Southern Meadow Pork</h1>
<p class="hero-sub">We are a new free range pig farm business.</p>
<a class="btn hero-btn">Contact Here</a>
<div class="dots" style="left:574px;top:652px"><span class="on"></span><span></span><span></span><span></span></div>

<section class="welcome">
  <div class="mascot" role="img" aria-label="Cartoon pig mascot standing with crossed arms"></div>
  <h2 class="welcome-h">WELCOME TO<small>SOUTHERN MEADOW PORK</small></h2>
  <div class="welcome-copy">
    <p>Lorem Ipsum is simply dummy text of the printing and typesetting industry. Lorem Ipsum has been the industry's standard dummy text ever since the 1500s, when an unknown printer took a galley of type and scrambled it to make a type specimen book. It has survived not only five centuries</p>
    <p>But also the leap into electronic typesetting, remaining essentially unchanged. It was popularised in the 1960s with the release of Letraset sheets containing Lorem Ipsum passages, and more recently with desktop publishing software like Aldus PageMaker including versions of Lorem Ipsum.</p>
  </div>
</section>

<section class="farm">
  <div class="farm-photo" role="img" aria-label="Two young pink piglets looking out of a pen"></div>
  <h2 class="farm-h">OUR FARM</h2>
  <div class="farm-copy">
    <p>Lorem Ipsum is simply dummy text of the printing and typesetting industry. Lorem Ipsum has been the industry's standard dummy text ever since the 1500s, when an unknown printer took a galley of type and scrambled it to make a type specimen book. It has survived not only five centuries, but also the leap into electronic typesetting, remaining essentially unchanged.</p>
    <p>It was popularised in the 1960s with the release of Letraset sheets containing Lorem Ipsum passages, and more recently with desktop publishing software like Aldus PageMaker including versions of Lorem Ipsum.</p>
  </div>
  <a class="btn farm-btn">Read More Info</a>
</section>

<section class="shop">
  <h2 class="shop-h">OUR FARM SHOP</h2>
  <p class="shop-intro">Lorem Ipsum is simply dummy text of the printing and typesetting industry. Lorem Ipsum has been the industry's standard dummy text ever since the 1500s, when an unknown printer took a galley of type and scrambled...</p>

  <article class="product" style="left:56px">
    <div class="product-photo" role="img" aria-label="Raw pork belly slices" style="background:radial-gradient(circle,#e9a3a0,#c8605e)"></div>
    <h3 class="product-name">2016 Harvest Salami Competition...</h3>
    <span class="price">$15.00</span>
    <a class="btn shop-btn">Shop Now</a>
  </article>
  <article class="product" style="left:421px">
    <div class="product-photo" role="img" aria-label="Pigs behind pen rails" style="background:radial-gradient(circle,#e0b3a8,#8d5e50)"></div>
    <h3 class="product-name">Fricandeaux</h3>
    <span class="price">$15.00</span>
    <a class="btn shop-btn">Shop Now</a>
  </article>
  <article class="product" style="left:784px">
    <div class="product-photo" role="img" aria-label="Raw pork fillet with herbs" style="background:radial-gradient(circle,#e6aaa8,#b9676a)"></div>
    <h3 class="product-name">Little French Ham</h3>
    <span class="price">$15.00</span>
    <a class="btn shop-btn">Shop Now</a>
  </article>

  <div class="dots" style="left:574px;top:724px"><span style="background:#a79d8c"></span><span style="background:#cfc6b2"></span><span style="background:#cfc6b2"></span><span style="background:#cfc6b2"></span></div>
</section>

<section class="testimonial">
  <div class="testimonial-photo" role="img" aria-label="Close-up of a pink pig resting on straw"></div>
  <svg class="quote-mark" width="46" height="38" viewBox="0 0 46 38" aria-hidden="true">
    <path d="M2 38V22C2 10 8 3 19 0l2 5c-6 2-9 6-9 12h9v21zM25 38V22C25 10 31 3 42 0l2 5c-6 2-9 6-9 12h9v21z" fill="#8f8178"/>
  </svg>
  <div class="testimonial-copy">
    <p>Lorem Ipsum is simply dummy text of the printing and typesetting industry. Lorem Ipsum has been the industry's standard dummy text ever since the 1500s, when an unknown printer took a galley of type and scrambled it to make a type specimen book,</p>
    <p>It has survived not only five centuries, but also the leap into electronic typesetting, remaining essentially unchanged.</p>
  </div>
  <div class="avatar" role="img" aria-label="Portrait of the customer"></div>
  <p class="person">Milo Harwick<span>Business man</span></p>
  <div class="dots" style="left:322px;top:544px"><span style="background:#8f8178"></span><span style="background:#8f8178"></span><span style="background:#8f8178"></span></div>
</section>

<footer class="site-footer">
  <div class="foot-col" style="left:100px">
    <h4 class="foot-h">Newsletter</h4>
    <p style="line-height:20px">Get our recent updates through your email id</p>
    <div class="email-field">Enter your email id</div>
    <a class="btn sub-btn">Subscribe</a>
  </div>
  <div class="foot-col" style="left:503px">
    <h4 class="foot-h">Welcome</h4>
    <ul><li>Home</li><li>About</li><li>Service</li><li>Shop</li><li>Contact</li></ul>
  </div>
  <div class="foot-col" style="left:666px">
    <h4 class="foot-h">Information</h4>
    <ul><li>Terms &amp; Conditions</li><li>Privacy Policy</li><li>Disclaimer</li><li>Sitemap</li></ul>
  </div>
  <div class="foot-col" style="left:873px">
    <h4 class="foot-h">Contact Info</h4>
    <p style="line-height:24px">120 Street name, City name,<br>Country name : 985666</p>
    <p class="contact-line" style="margin-top:6px">
      <svg width="14" height="14" viewBox="0 0 24 24" aria-hidden="true"><path d="M6.6 10.8a15 15 0 006.6 6.6l2.2-2.2c.3-.3.7-.4 1-.2 1.1.4 2.3.6 3.6.6.6 0 1 .4 1 1V20c0 .6-.4 1-1 1C10.6 21 3 13.4 3 4c0-.6.4-1 1-1h3.5c.6 0 1 .4 1 1 0 1.3.2 2.5.6 3.6.1.3 0 .7-.2 1z" fill="var(--green)"/></svg>
      (985) 412-3067
    </p>
    <p class="contact-line">
      <svg width="14" height="14" viewBox="0 0 24 24" aria-hidden="true"><rect x="2" y="5" width="20" height="14" rx="2" fill="none" stroke="var(--green)" stroke-width="2"/><path d="M2 6l10 7 10-7" fill="none" stroke="var(--green)" stroke-width="2"/></svg>
      info@southernmeadowpork.com
    </p>
  </div>
  <p class="copyright">Copyright © Southern Meadow Pork. 2016 . All Rights Reserved</p>
</footer>

</body>
</html>
```